Seeking a new website design for electrical contracting company

Brisket & Vane electrical contracting needs a new website for brisket-vane.example

We are looking for modern and something real cool with motion for a landing page. we have some cool images from our photo shoot. maybe even 3d motion our existing logo. we would like something we can edit with news and events and update a past project page. Also allow to take payment
stock images at
https://lorapellwinphotos.picvault-demo.example/Brisket-and-Vane

Target Market(s)

construction , home owners , business owners,

Industry/Entity Type

construction , electrical

Coding

Number of Pages Required

5+ page

Font styles to use
Serif
Sans Serif

Colors
0054AA
0677BA
7BADD7
CADEEF
E8F1F8
0094D4
00A9DD
6FCCEA
C7EBF8
E9F6FB
FFF300
FFF600
FEFA6F
FFFEC7
FFFEE8

Requirements
Must have
• excitement, motion, selling professionalism,

```html
<!DOCTYPE html>
<html lang="en">
<head>
<meta charset="utf-8">
<title>Brisket &amp; Vane Electrical Contractors</title>
<link href="https://fonts.googleapis.com/css2?family=Josefin+Sans:wght@400;600;700&family=Lato:wght@400;700&display=swap" rel="stylesheet">
<style>
:root{
  --navy:#1f2b6f;
  --navy-deep:#19235c;
  --orange:#f5891f;
  --orange-dark:#e0741a;
  --lavender:#eceffc;
  --ink:#23242c;
  --muted:#5c5f6e;
  --line:#d9dbe6;
  --white:#ffffff;
}
*{box-sizing:border-box;margin:0;padding:0}
html,body{width:1200px;height:4601px;overflow:hidden;background:var(--white)}
body{font-family:"Lato",sans-serif;color:var(--ink);position:relative}
.page{position:relative;width:1200px;height:4601px;overflow:hidden}
.abs{position:absolute}
.display{font-family:"Josefin Sans",sans-serif}
.btn{position:absolute;background:var(--orange);color:var(--white);font-family:"Josefin Sans",sans-serif;font-weight:700;font-size:15px;border-radius:6px;display:flex;align-items:center;justify-content:center;letter-spacing:.5px;box-shadow:0 0 0 2px rgba(245,137,31,.25)}
.photo{position:absolute}

.topbar{position:absolute;top:0;left:0;width:1200px;height:33px;background:var(--navy)}
.topbar-left{position:absolute;left:0;top:0;width:425px;height:33px;background:var(--orange)}
.topbar-text{position:absolute;top:8px;color:var(--white);font-family:"Josefin Sans",sans-serif;font-weight:600;font-size:14px;display:flex;align-items:center;gap:10px}
.topbar-divider{position:absolute;left:979px;top:8px;width:2px;height:17px;background:var(--white)}
.social{position:absolute;display:flex;gap:5px}
.social span{display:block;border-radius:50%;background:var(--white)}

.nav{position:absolute;top:33px;left:0;width:1200px;height:71px;background:var(--white);z-index:3}
.brand-tab{position:absolute;left:95px;top:33px;width:305px;height:100px;background:var(--white);clip-path:polygon(0 0,100% 0,100% 72%,50% 100%,0 72%);z-index:3}
.brand{position:absolute;left:111px;top:55px;display:flex;align-items:center;gap:10px;z-index:4}
.brand-mark{width:44px;height:44px;background:var(--navy);border-radius:6px}
.brand-name{font-family:"Josefin Sans",sans-serif;font-weight:700;font-size:24px;color:var(--navy);white-space:nowrap}
.nav-links{position:absolute;top:66px;left:0;z-index:4}
.nav-links a{position:absolute;font-family:"Josefin Sans",sans-serif;font-size:16px;color:var(--ink);text-decoration:none;white-space:nowrap}
.nav-links a.active{color:var(--orange);font-weight:600}

.hero{position:absolute;top:104px;left:0;width:1200px;height:664px;background:var(--navy);clip-path:polygon(0 0,100% 0,100% 530px,50% 664px,0 530px);overflow:hidden}
.hero-photo{position:absolute;left:470px;top:0;width:730px;height:664px;background:linear-gradient(90deg,var(--navy) 0%,rgba(31,43,111,.6) 22%,rgba(90,96,120,.3) 45%,#8b8e98 70%,#b7b3ac 100%),linear-gradient(180deg,#6d7486,#3f4560)}
.hero-title{position:absolute;left:111px;top:258px;font-family:"Josefin Sans",sans-serif;font-weight:700;font-size:58px;line-height:77px;letter-spacing:3px;color:var(--white);text-transform:uppercase}
.hero-title .accent{color:var(--orange)}

.hex{position:absolute}
.hex-label{position:absolute;width:100%;text-align:center;font-family:"Josefin Sans",sans-serif;font-size:17px;line-height:22px}

.about-big{position:absolute;left:452px;top:940px;font-family:"Josefin Sans",sans-serif;font-weight:700;font-size:54px;color:var(--orange)}
.about-years{position:absolute;left:453px;top:1010px;font-family:"Josefin Sans",sans-serif;font-size:25px;line-height:35px;color:var(--ink)}
.section-title{position:absolute;font-family:"Josefin Sans",sans-serif;font-size:43px;color:var(--ink);white-space:nowrap;display:flex;align-items:center;gap:10px}
.section-title b{color:var(--navy);font-weight:700}
.about-text{position:absolute;left:646px;top:988px;width:448px;font-size:15px;line-height:32.5px;color:var(--muted)}
.about-text p+p{margin-top:5px}

.band{position:absolute;left:0;width:1200px;background:var(--lavender)}
.service-card{position:absolute;top:1586px;width:322px;height:450px;background:var(--white);border-radius:6px;box-shadow:0 6px 20px rgba(31,43,111,.08)}
.service-card .photo{left:9px;top:9px;width:304px;height:270px;border-radius:3px}
.service-card h3{position:absolute;left:0;width:100%;text-align:center;font-family:"Josefin Sans",sans-serif;font-weight:600;font-size:17px;color:var(--ink)}
.service-card p{position:absolute;left:22px;width:278px;text-align:center;font-size:12.5px;line-height:27px;color:var(--muted)}
.arrow{position:absolute;width:22px;height:22px;border-radius:50%;display:flex;align-items:center;justify-content:center}
.arrow.dark{background:var(--navy)}
.arrow.light{background:#dcdfee}

.avatar{position:absolute;width:78px;height:78px;border-radius:50%;border:3px solid var(--white);box-shadow:0 2px 8px rgba(0,0,0,.15)}
.t-name{position:absolute;font-size:17px;color:var(--ink)}
.stars{position:absolute;color:var(--orange);font-size:19px;letter-spacing:1px}
.quote-mark{position:absolute;font-family:Georgia,serif;font-weight:700;font-size:74px;line-height:1;color:var(--orange)}
.t-text{position:absolute;font-size:12.5px;line-height:25px;color:var(--muted)}
.t-divider{position:absolute;left:594px;top:2297px;height:168px;border-left:3px dashed #c9cbd6}

.project-frame{position:absolute;left:39px;top:2661px;width:1131px;height:636px;background:var(--white);box-shadow:0 4px 18px rgba(31,43,111,.08)}
.tile{position:absolute}
.tile-hover{position:absolute;left:423px;top:2674px;width:356px;height:303px;background:rgba(31,43,111,.92)}
.tile-hover .frame{position:absolute;left:12px;top:12px;right:12px;bottom:12px;border:2px solid rgba(255,255,255,.85)}

.blog-intro{position:absolute;left:598px;top:3482px;width:496px;font-size:12.5px;line-height:26px;color:var(--muted)}
.blog-card{position:absolute;top:3584px;width:315px;height:375px;background:var(--white);box-shadow:0 4px 16px rgba(31,43,111,.1)}
.blog-card .photo{left:0;top:0;width:315px;height:211px}
.blog-cat{position:absolute;left:14px;top:233px;font-family:"Josefin Sans",sans-serif;font-weight:700;font-size:14px;color:var(--navy-deep);letter-spacing:.5px}
.blog-title{position:absolute;left:14px;top:258px;width:290px;font-size:15.5px;line-height:27px;color:var(--ink)}
.blog-meta{position:absolute;left:16px;top:323px;display:flex;gap:34px;font-size:12px;color:var(--muted)}
.blog-meta span{display:flex;align-items:center;gap:6px}

.footer-head{position:absolute;font-family:"Josefin Sans",sans-serif;font-weight:600;font-size:21px;color:var(--white)}
.footer-list{position:absolute;list-style:none}
.footer-list li{font-size:16px;line-height:32px;color:var(--white)}
.contact-row{position:absolute;left:530px;display:flex;gap:20px;font-size:16px;line-height:27px;color:var(--white)}
.contact-row svg{flex:none;margin-top:5px}
.footer-input{position:absolute;left:825px;top:4340px;width:268px;height:37px;background:var(--white);border-radius:4px;font-size:12px;color:#777;padding:12px 16px}
.footer-rule{position:absolute;left:111px;top:4563px;width:985px;height:1px;background:rgba(255,255,255,.45)}
.copyright{position:absolute;left:0;top:4575px;width:1200px;text-align:center;font-size:13px;color:var(--white)}
</style>
</head>
<body>
<div class="page">

  <div class="topbar">
    <div class="topbar-left"></div>
    <div class="topbar-text" style="left:116px">
      <svg width="16" height="16" viewBox="0 0 24 24"><path fill="#fff" d="M6.6 10.8a15 15 0 0 0 6.6 6.6l2.2-2.2c.3-.3.7-.4 1-.2 1.1.4 2.3.6 3.6.6.6 0 1 .4 1 1V20c0 .6-.4 1-1 1A17 17 0 0 1 3 4c0-.6.4-1 1-1h3.5c.6 0 1 .4 1 1 0 1.3.2 2.5.6 3.6.1.3 0 .7-.2 1z"/></svg>
      <span>Client Services &nbsp;1-555-014-2290</span>
    </div>
    <div class="topbar-text" style="left:720px">
      <svg width="17" height="13" viewBox="0 0 17 13"><rect x="0.5" y="0.5" width="16" height="12" fill="#fff"/><path d="M1 1l7.5 6L16 1" stroke="#1f2b6f" stroke-width="1.4" fill="none"/></svg>
      <span><b>Email:</b> <span style="font-weight:400">jay@brisket-vane.example</span></span>
    </div>
    <div class="topbar-divider"></div>
    <div class="social" style="left:1009px;top:7px">
      <span style="width:19px;height:19px"></span><span style="width:19px;height:19px"></span><span style="width:19px;height:19px"></span><span style="width:19px;height:19px"></span><span style="width:19px;height:19px"></span>
    </div>
  </div>

  <div class="nav"></div>
  <div class="brand-tab"></div>
  <div class="brand"><span class="brand-mark"></span><span class="brand-name">Brisket &amp; Vane</span></div>
  <svg class="abs" style="left:481px;top:40px;z-index:4" width="9" height="20" viewBox="0 0 9 20"><path d="M6 0L0 11h4l-2 9 7-12H5z" fill="#f5891f"/></svg>
  <nav class="nav-links">
    <a class="active" style="left:459px">Home</a>
    <a style="left:536px">About</a>
    <a style="left:613px">Services</a>
    <a style="left:705px">Projects</a>
    <a style="left:795px">Our Team</a>
    <a style="left:902px">Blog</a>
  </nav>
  <div class="btn" style="left:973px;top:55px;width:117px;height:38px;z-index:4;font-weight:600;font-size:16px">Contact Us</div>

  <section class="hero">
    <div class="hero-photo" role="img" aria-label="Electrician in hard hat and orange safety vest working on a control panel"></div>
  </section>
  <h1 class="hero-title">Lighting the<br>future of <span class="accent">electrical</span><br><span class="accent">contracting.</span></h1>
  <div class="btn" style="left:111px;top:503px;width:119px;height:37px;font-weight:600">Get Started</div>

  <svg class="hex" style="left:262px;top:594px" width="204" height="234" viewBox="0 0 204 234">
    <polygon points="102,4 200,60 200,174 102,230 4,174 4,60" fill="#fff" stroke="#fff" stroke-width="6" style="filter:drop-shadow(0 4px 10px rgba(0,0,0,.12))"/>
    <polygon points="102,12 192,64 192,170 102,222 12,170 12,64" fill="#fff" stroke="#f5891f" stroke-width="3"/>
    <circle cx="102" cy="80" r="27" fill="#f5891f"/>
    <circle cx="102" cy="80" r="15" fill="none" stroke="#fff" stroke-width="2.5"/>
    <path d="M102 71v10l6 4" stroke="#fff" stroke-width="2.5" fill="none" stroke-linecap="round"/>
  </svg>
  <div class="hex-label" style="left:262px;top:715px;width:204px;color:#23242c">Ontime at Services</div>

  <svg class="hex" style="left:488px;top:652px" width="212" height="236" viewBox="0 0 212 236">
    <polygon points="106,4 206,62 206,174 106,232 6,174 6,62" fill="#f5891f"/>
    <polygon points="106,20 192,70 192,166 106,216 20,166 20,70" fill="#1f2b6f"/>
    <circle cx="106" cy="76" r="24" fill="#fff"/>
    <circle cx="106" cy="76" r="15" fill="none" stroke="#1f2b6f" stroke-width="2.5"/>
    <text x="106" y="81" text-anchor="middle" font-family="Josefin Sans, sans-serif" font-weight="700" font-size="12" fill="#1f2b6f">24</text>
  </svg>
  <div class="hex-label" style="left:488px;top:768px;width:212px;color:#fff;font-weight:600">24/7 Services</div>

  <svg class="hex" style="left:719px;top:590px" width="204" height="234" viewBox="0 0 204 234">
    <polygon points="102,4 200,60 200,174 102,230 4,174 4,60" fill="#fff" stroke="#fff" stroke-width="6" style="filter:drop-shadow(0 4px 10px rgba(0,0,0,.12))"/>
    <polygon points="102,12 192,64 192,170 102,222 12,170 12,64" fill="#fff" stroke="#f5891f" stroke-width="3"/>
    <circle cx="102" cy="78" r="27" fill="#f5891f"/>
    <circle cx="102" cy="73" r="11" fill="none" stroke="#fff" stroke-width="2.5"/>
    <path d="M95 82l-4 14 6-3 5 5M109 82l4 14-6-3-5 5" stroke="#fff" stroke-width="2" fill="none"/>
  </svg>
  <div class="hex-label" style="left:719px;top:712px;width:204px;color:#23242c">Verified<br>Professionals</div>

  <div class="photo" style="left:111px;top:934px;width:309px;height:427px;background:linear-gradient(160deg,#8c93a6,#5b6278 55%,#c9a27a)" role="img" aria-label="Gloved hands testing wiring in an electrical panel"></div>
  <div class="photo" style="left:240px;top:1087px;width:364px;height:280px;background:#fff"></div>
  <div class="photo" style="left:246px;top:1093px;width:352px;height:268px;background:linear-gradient(180deg,#9cc1e6 0%,#c8dcef 55%,#8e9a6f 100%)" role="img" aria-label="Two workers in hard hats and safety vests shaking hands under a power pylon"></div>
  <div class="about-big">10+</div>
  <div class="about-years">Years<br>Experience</div>

  <h2 class="section-title" style="left:646px;top:928px">About <b>Us</b>
    <svg width="18" height="44" viewBox="0 0 18 44"><path d="M13 0L1 24h8L4 44 17 17H9z" fill="#f5891f"/></svg>
  </h2>
  <div class="about-text">
    <p>We're more than just electricians — we're problem solvers, system designers, and project partners. Whether it's powering a new commercial high-rise or upgrading critical infrastructure, we bring deep expertise, attention to detail, and a relentless drive for quality.</p>
    <p>Our success is built on relationships. With our clients. With our crews. And with the communities we help grow — one circuit at a time.</p>
  </div>
  <div class="btn" style="left:646px;top:1272px;width:117px;height:37px;font-weight:600">Read More</div>

  <div class="band" style="top:1447px;height:665px;clip-path:polygon(86px 0,100% 0,100% 100%,0 100%,0 88px)"></div>
  <h2 class="section-title" style="left:470px;top:1496px">What <b>We Do</b>
    <svg width="18" height="44" viewBox="0 0 18 44"><path d="M13 0L1 24h8L4 44 17 17H9z" fill="#f5891f"/></svg>
  </h2>

  <div class="arrow light" style="left:29px;top:1799px"><svg width="8" height="10" viewBox="0 0 8 10"><path d="M6 1L2 5l4 4" stroke="#fff" stroke-width="2" fill="none"/></svg></div>
  <div class="arrow light" style="left:1136px;top:1799px"><svg width="8" height="10" viewBox="0 0 8 10"><path d="M2 1l4 4-4 4" stroke="#fff" stroke-width="2" fill="none"/></svg></div>

  <article class="service-card" style="left:102px">
    <div class="photo" style="background:linear-gradient(160deg,#9aa6b8,#4f5d73 60%,#c7742c)" role="img" aria-label="Technician in orange vest inspecting factory machinery"></div>
    <h3 style="top:300px">Commercial Electrical Contracting</h3>
    <p style="top:333px">End-to-end electrical systems for offices, retail, mixed-use, and high-rise buildings. Efficient, code-compliant, and built to scale.</p>
  </article>
  <article class="service-card" style="left:438px">
    <div class="photo" style="background:linear-gradient(160deg,#5e6a78,#2e3644 55%,#8c6a4f)" role="img" aria-label="Smiling technicians giving a thumbs up beside an industrial fan"></div>
    <svg class="abs" style="left:129px;top:252px" width="64" height="64" viewBox="0 0 64 64"><circle cx="32" cy="32" r="31" fill="#fff"/><rect x="20" y="24" width="24" height="20" fill="none" stroke="#f5891f" stroke-width="2.5"/><path d="M24 24v-6h6v6M36 24v-8h6v8M24 31h16M24 37h16" stroke="#f5891f" stroke-width="2" fill="none"/></svg>
    <h3 style="top:316px;color:#1f2b6f">Industrial Electrical Services</h3>
    <p style="top:339px">Heavy-duty power systems, automation wiring, and equipment installs for factories, warehouses, and energy facilities.</p>
  </article>
  <article class="service-card" style="left:773px">
    <div class="photo" style="background:linear-gradient(160deg,#d6d6d8,#a9a7a5 55%,#c8a38a)" role="img" aria-label="Hands fitting a wall socket with a screwdriver"></div>
    <h3 style="top:300px">Service &amp; Maintenance Contracts</h3>
    <p style="top:333px">Preventive maintenance, emergency repairs, and system checks to keep your infrastructure running.</p>
  </article>

  <h2 class="section-title" style="left:387px;top:2191px">Client <b>Testimonials</b>
    <svg width="18" height="44" viewBox="0 0 18 44"><path d="M13 0L1 24h8L4 44 17 17H9z" fill="#f5891f"/></svg>
  </h2>
  <div class="arrow dark" style="left:43px;top:2377px"><svg width="8" height="10" viewBox="0 0 8 10"><path d="M6 1L2 5l4 4" stroke="#fff" stroke-width="2" fill="none"/></svg></div>
  <div class="arrow light" style="left:1121px;top:2377px"><svg width="8" height="10" viewBox="0 0 8 10"><path d="M2 1l4 4-4 4" stroke="#fff" stroke-width="2" fill="none"/></svg></div>

  <div class="avatar" style="left:110px;top:2307px;background:linear-gradient(160deg,#e6e6e6,#b9b0a6)" role="img" aria-label="Portrait of client Dana R."></div>
  <div class="t-name" style="left:214px;top:2321px">~Dana R., Project Manager,</div>
  <div class="stars" style="left:213px;top:2347px">★★★★★</div>
  <div class="quote-mark" style="left:518px;top:2318px">”</div>
  <div class="t-text" style="left:111px;top:2397px;width:460px">"Brisket &amp; Vane delivered our project ahead of schedule and under budget. Their crew was professional, safe, and a pleasure to work with."</div>

  <div class="t-divider"></div>

  <div class="avatar" style="left:636px;top:2307px;background:linear-gradient(160deg,#6d7a4e,#3d4a2c)" role="img" aria-label="Portrait of client Owen T."></div>
  <div class="t-name" style="left:741px;top:2321px">~Owen T., Facilities Director</div>
  <div class="stars" style="left:740px;top:2347px">★★★★★</div>
  <div class="quote-mark" style="left:1045px;top:2318px">”</div>
  <div class="t-text" style="left:641px;top:2408px;width:460px">Top-tier work. From design to final inspection, everything was handled with precision. Wouldn't trust anyone else with our electrical systems."</div>

  <div class="band" style="top:2554px;height:843px;clip-path:polygon(86px 0,100% 0,100% calc(100% - 86px),calc(100% - 86px) 100%,0 100%,0 88px)"></div>
  <h2 class="section-title" style="left:437px;top:2579px">Latest <b>Projetcs</b>
    <svg width="18" height="44" viewBox="0 0 18 44"><path d="M13 0L1 24h8L4 44 17 17H9z" fill="#f5891f"/></svg>
  </h2>
  <div class="project-frame"></div>
  <div class="tile" style="left:52px;top:2674px;width:355px;height:303px;background:linear-gradient(160deg,#e2e2e2,#a9a9ad 60%,#4a4a52)" role="img" aria-label="Electrician on a ladder fitting overhead conduit"></div>
  <div class="tile" style="left:423px;top:2674px;width:356px;height:303px;background:linear-gradient(160deg,#7d89a8,#3d4a6e)" role="img" aria-label="Industrial control room equipment"></div>
  <div class="tile-hover"><div class="frame"></div></div>
  <div class="abs display" style="left:423px;top:2785px;width:356px;text-align:center;color:#f5891f;font-size:15px;font-weight:600;letter-spacing:.5px">Service &amp; Maintenance Contracts</div>
  <div class="abs display" style="left:423px;top:2816px;width:356px;text-align:center;color:#fff;font-size:25px;font-weight:600;letter-spacing:.5px">Industrial Maintenance</div>
  <div class="abs" style="left:561px;top:2860px;width:80px;height:3px;background:#f5891f"></div>
  <div class="tile" style="left:797px;top:2674px;width:357px;height:303px;background:linear-gradient(160deg,#8fa7c8,#5f7390 50%,#9aa92f)" role="img" aria-label="Engineers in high-visibility gear at a wind turbine"></div>
  <div class="tile" style="left:52px;top:2983px;width:355px;height:303px;background:linear-gradient(160deg,#c9c6bd,#8a8a88 55%,#2c2f3a)" role="img" aria-label="Electrician routing thick cables on a wall"></div>
  <div class="tile" style="left:423px;top:2983px;width:356px;height:303px;background:linear-gradient(160deg,#c9d3cf,#7f8f8a 50%,#c83a3a)" role="img" aria-label="Hands stripping a wire with pliers"></div>
  <div class="tile" style="left:797px;top:2983px;width:357px;height:303px;background:linear-gradient(160deg,#9aa6b8,#4f5d73 60%,#c7742c)" role="img" aria-label="Technician in orange vest at factory machinery"></div>
  <div class="btn" style="left:523px;top:3329px;width:154px;height:36px;font-weight:600">View All Projects</div>

  <h2 class="section-title" style="left:111px;top:3476px;font-size:45px">Latest <b>News &amp; Blog</b>
    <svg width="18" height="44" viewBox="0 0 18 44"><path d="M13 0L1 24h8L4 44 17 17H9z" fill="#f5891f"/></svg>
  </h2>
  <p class="blog-intro">Lorem ipsum dolor sit amet, consectetur adipiscing elit, sed do eiusmod tempor incididunt ut labore et dolore magna aliqua. Ut enim ad minim veniam, quis nostrud exercitation ullamco laboris nisi ut aliquip ex ea commodo consequat.</p>

  <div class="arrow dark" style="left:46px;top:3711px"><svg width="8" height="10" viewBox="0 0 8 10"><path d="M6 1L2 5l4 4" stroke="#fff" stroke-width="2" fill="none"/></svg></div>
  <div class="arrow light" style="left:1126px;top:3711px"><svg width="8" height="10" viewBox="0 0 8 10"><path d="M2 1l4 4-4 4" stroke="#fff" stroke-width="2" fill="none"/></svg></div>

  <article class="blog-card" style="left:114px">
    <div class="photo" style="background:linear-gradient(160deg,#a9b3c4,#3f4f78 60%,#d7772a)" role="img" aria-label="Electrician measuring a panel with a multimeter"></div>
    <div class="blog-cat">Maintenance</div>
    <div class="blog-title">Upgrading Legacy Systems: How We Modernized a 1960s Industrial Plant</div>
    <div class="blog-meta">
      <span><svg width="14" height="13" viewBox="0 0 14 13"><rect x="1" y="2" width="12" height="10" fill="none" stroke="#777" stroke-width="1.3"/><path d="M1 5h12" stroke="#777" stroke-width="1.3"/></svg>Apr 21,2025</span>
      <span><svg width="18" height="12" viewBox="0 0 18 12"><rect x="1" y="1" width="16" height="10" rx="2" fill="none" stroke="#777" stroke-width="1.3"/></svg>4 Comments</span>
    </div>
  </article>
  <article class="blog-card" style="left:443px">
    <div class="photo" style="background:linear-gradient(160deg,#8e96a5,#3b4360 60%,#2c3550)" role="img" aria-label="Two engineers reviewing a clipboard at a switchboard"></div>
    <div class="blog-cat">Tool BOx Checking</div>
    <div class="blog-title">Toolbox Talk: New OSHA Safety Guidelines for 2025</div>
    <div class="blog-meta">
      <span><svg width="14" height="13" viewBox="0 0 14 13"><rect x="1" y="2" width="12" height="10" fill="none" stroke="#777" stroke-width="1.3"/><path d="M1 5h12" stroke="#777" stroke-width="1.3"/></svg>Apr 18,2025</span>
      <span><svg width="18" height="12" viewBox="0 0 18 12"><rect x="1" y="1" width="16" height="10" rx="2" fill="none" stroke="#777" stroke-width="1.3"/></svg>4 Comments</span>
    </div>
  </article>
  <article class="blog-card" style="left:772px">
    <div class="photo" style="background:linear-gradient(160deg,#9ea8ba,#3a4468 60%,#e0b43a)" role="img" aria-label="Crew in hard hats gathered around a tablet"></div>
    <div class="blog-cat">Service</div>
    <div class="blog-title">The Future of Commercial Electrical: Smart Panels &amp; Load Management</div>
    <div class="blog-meta">
      <span><svg width="14" height="13" viewBox="0 0 14 13"><rect x="1" y="2" width="12" height="10" fill="none" stroke="#777" stroke-width="1.3"/><path d="M1 5h12" stroke="#777" stroke-width="1.3"/></svg>Apr 17,2025</span>
      <span><svg width="18" height="12" viewBox="0 0 18 12"><rect x="1" y="1" width="16" height="10" rx="2" fill="none" stroke="#777" stroke-width="1.3"/></svg>4 Comments</span>
    </div>
  </article>

  <svg class="abs" style="left:0;top:4040px" width="1200" height="561" viewBox="0 0 1200 561">
    <polygon points="250,95 607,5 980,95 960,100 607,30 270,100" fill="#f5891f"/>
    <polygon points="0,170 607,28 1200,160 1200,561 0,561" fill="#1f2b6f"/>
  </svg>
  <div class="abs" style="left:0;top:4165px;width:1200px;display:flex;justify-content:center;align-items:center;gap:16px">
    <span style="width:86px;height:86px;background:#fff;border-radius:8px"></span>
    <span class="display" style="font-weight:700;font-size:44px;color:#fff;white-space:nowrap">Brisket &amp; Vane</span>
  </div>

  <div class="footer-head" style="left:112px;top:4296px">Quick Links</div>
  <ul class="footer-list" style="left:116px;top:4331px">
    <li>Home</li><li>About</li><li>Services</li><li>Projects</li><li>Our Team</li><li>Blog</li><li>Contact Us</li>
  </ul>
  <div class="footer-head" style="left:310px;top:4296px">Help Links</div>
  <ul class="footer-list" style="left:313px;top:4331px">
    <li>Privacy Policy</li><li>Terms &amp; Conditions</li><li>Disclaimer</li><li>FAQ's</li><li>Support</li><li>Help</li>
  </ul>
  <div class="footer-head" style="left:531px;top:4296px">Contact Info</div>
  <div class="contact-row" style="top:4341px">
    <svg width="16" height="16" viewBox="0 0 24 24"><path fill="#fff" d="M6.6 10.8a15 15 0 0 0 6.6 6.6l2.2-2.2c.3-.3.7-.4 1-.2 1.1.4 2.3.6 3.6.6.6 0 1 .4 1 1V20c0 .6-.4 1-1 1A17 17 0 0 1 3 4c0-.6.4-1 1-1h3.5c.6 0 1 .4 1 1 0 1.3.2 2.5.6 3.6.1.3 0 .7-.2 1z"/></svg>
    <span>1-555-014-2290</span>
  </div>
  <div class="contact-row" style="top:4378px">
    <svg width="16" height="12" viewBox="0 0 17 13"><rect x="0.5" y="0.5" width="16" height="12" fill="#fff"/><path d="M1 1l7.5 6L16 1" stroke="#1f2b6f" stroke-width="1.4" fill="none"/></svg>
    <span>jay@brisket-vane.example</span>
  </div>
  <div class="contact-row" style="top:4420px">
    <svg width="16" height="18" viewBox="0 0 16 20"><path fill="#fff" d="M8 0a7 7 0 0 0-7 7c0 5 7 13 7 13s7-8 7-13a7 7 0 0 0-7-7zm0 10a3 3 0 1 1 0-6 3 3 0 0 1 0 6z"/></svg>
    <span>48 Alder Ct. Fairhollow<br>NH 03000</span>
  </div>

  <div class="footer-head" style="left:823px;top:4287px">Newsletter Sign Up</div>
  <div class="footer-input">Enter Email Addrtess</div>
  <div class="btn" style="left:825px;top:4390px;width:118px;height:36px;font-weight:600">Subscribe</div>
  <div class="social" style="left:823px;top:4465px;gap:7px">
    <span style="width:30px;height:30px;background:#f5891f"></span><span style="width:30px;height:30px"></span><span style="width:30px;height:30px"></span><span style="width:30px;height:30px"></span><span style="width:30px;height:30px"></span>
  </div>

  <div class="footer-rule"></div>
  <div class="copyright">© 2025 Brisket &amp; Vane Electrical Contractors. All rights reserved.</div>

</div>
</body>
</html>
```